Builder of high-end, expensive tables and other furniture

Build a website that represents what we do. I want a luxury feel that appeals to those who can afford our products. We build very high end tables and other furniture using trees that have fallen or are standing dead. We never cut living trees. Trees are harvested, milled, and kiln dried. Then that lumber is meticulously turned into fine furniture using the best equipment. Our furniture prices range from $1,000-$20,000.

Trying to figure out how to raise my spend.

```html
<!DOCTYPE html>
<html lang="en">
<head>
<meta charset="utf-8">
<title>Heartwood Tables</title>
<link href="https://fonts.googleapis.com/css2?family=Poppins:wght@400;500;600;700;800&display=swap" rel="stylesheet">
<style>
:root{
  --orange:#ef7338;
  --ink:#111111;
  --muted:#6f6f76;
  --mist:#f1f2f8;
  --white:#ffffff;
  --black:#000000;
}
*{box-sizing:border-box;margin:0;padding:0}
html,body{width:1200px;height:3559px;overflow:hidden}
body{position:relative;font-family:"Poppins",sans-serif;color:var(--ink);background:var(--white)}
.abs{position:absolute}
.btn{position:absolute;display:flex;align-items:center;justify-content:center;background:var(--orange);color:var(--white);font-weight:600;font-size:15px;text-decoration:none}
.btn--outline{background:transparent;border:2px solid var(--white)}
/* header */
.site-header{position:absolute;left:0;top:0;width:1200px;height:84px;background:var(--white)}
.brand{position:absolute;display:flex;align-items:center;gap:10px;font-weight:600;font-size:28px;color:var(--orange)}
.brand__dot{width:14px;height:14px;border-radius:50%;background:var(--orange)}
.main-nav{position:absolute;left:464px;top:31px;display:flex;gap:23px;font-size:15px;font-weight:600}
.main-nav a{color:var(--ink);text-decoration:none}
/* hero */
.hero{position:absolute;left:0;top:84px;width:1200px;height:558px;background:linear-gradient(90deg,#8d8f92 0%,#5c5d60 30%,#4a4a4c 55%,#c9c8c4 80%,#e3e2df 100%)}
.hero__floor{position:absolute;left:0;bottom:0;width:1200px;height:170px;background:linear-gradient(180deg,#6b5646,#4a3a2e)}
.hero__title{position:absolute;left:115px;top:130px;color:var(--white);font-weight:800;font-size:51px;line-height:52px;text-transform:uppercase}
/* mist section */
.mist{position:absolute;left:0;top:642px}
.photo{position:absolute}
.section-title{position:absolute;font-weight:700;font-size:36px;line-height:44px}
.copy{position:absolute;font-size:14.5px;line-height:25.6px;color:var(--muted)}
/* products */
.price-panel{position:absolute;left:97px;top:1602px;width:320px;height:398px;background:var(--white)}
.panel-title{position:absolute;left:14px;top:28px;font-weight:600;font-size:23px}
.panel-sub{position:absolute;left:16px;top:70px;font-size:14px}
.range-label{position:absolute;top:140px;font-size:13px}
.field-label{position:absolute;left:19px;font-weight:500;font-size:15px}
.field{position:absolute;left:14px;width:285px;height:50px;border:1.5px solid #333;font-weight:600;font-size:15px}
.field span{position:absolute;left:4px;top:14px}
.field i{position:absolute;right:48px;top:10px;width:1px;height:30px;background:#333}
.field b{position:absolute;right:18px;top:14px}
.product{position:absolute;overflow:hidden}
.product h3{position:absolute;left:15px;top:26px;font-weight:600;font-size:23px}
.product p{position:absolute;left:16px;top:70px;font-size:14px}
.product strong{position:absolute;left:19px;top:99px;font-weight:600;font-size:16px}
/* features */
.feature{position:absolute;top:2693px;width:200px}
.feature svg{display:block;height:60px}
.feature h4{margin-top:22px;font-weight:700;font-size:24px}
.feature p{margin-top:6px;font-size:14px;line-height:25.6px;color:var(--muted)}
/* band */
.promise{position:absolute;left:0;top:3001px;width:1200px;height:345px;background:var(--orange);color:var(--white);text-align:center}
.promise h2{position:absolute;left:0;top:60px;width:1200px;font-weight:700;font-size:35px;line-height:38px}
.promise p{position:absolute;left:190px;top:145px;width:820px;font-size:14px;line-height:25.6px}
/* footer */
.site-footer{position:absolute;left:0;top:3346px;width:1200px;height:213px;background:var(--black);color:var(--white)}
.social{position:absolute;left:548px;top:107px;display:flex;gap:21px}
.social span{width:23px;height:23px;border:1.5px solid var(--white);border-radius:50%}
.foot-nav{position:absolute;left:0;top:148px;width:1200px;display:flex;justify-content:center;gap:26px;font-weight:600;font-size:15px}
.copyright{position:absolute;left:0;top:184px;width:1200px;text-align:center;font-size:13px}
</style>
</head>
<body>

<header class="site-header">
  <div class="brand" style="left:112px;top:18px"><span class="brand__dot"></span>Heartwood Tables</div>
  <nav class="main-nav"><a href="#">What We Do</a><a href="#">Our Products</a><a href="#">Shop</a><a href="#">Support</a><a href="#">Contact us</a></nav>
  <svg class="abs" style="left:1000px;top:30px" width="26" height="26" viewBox="0 0 26 26" aria-label="Search"><circle cx="10.5" cy="10.5" r="8" fill="none" stroke="#111" stroke-width="2.4"/><line x1="16.5" y1="16.5" x2="24" y2="24" stroke="#111" stroke-width="2.6"/></svg>
  <svg class="abs" style="left:1057px;top:30px" width="22" height="20" viewBox="0 0 22 20" aria-label="Cart"><path d="M0 2h4l3 11h11l3-8H6" fill="none" stroke="#111" stroke-width="2.2"/><path d="M6 5h15l-3 8H8z" fill="#111"/><circle cx="9" cy="17" r="2" fill="#111"/><circle cx="17" cy="17" r="2" fill="#111"/></svg>
</header>

<section class="hero" role="img" aria-label="Modern office interior with a wooden desk, computer and chairs beside tall windows">
  <div class="hero__floor"></div>
  <h1 class="hero__title">Welcome to<br>Heartwood Tables</h1>
  <a class="btn" href="#" style="left:115px;top:265px;width:138px;height:47px">Contact Us</a>
</section>

<svg class="mist" width="1200" height="1970" viewBox="0 0 1200 1970" aria-hidden="true"><path d="M0 0H1200V1844Q600 2096 0 1844Z" fill="#f1f2f8"/></svg>

<div class="photo" role="img" aria-label="Dining room with a live-edge wooden table, chairs and hanging fern" style="left:113px;top:735px;width:407px;height:405px;background:linear-gradient(160deg,#e9e8e3,#c9c2b5 55%,#8b6b4c)"></div>
<h2 class="section-title" style="left:603px;top:742px">What We Do</h2>
<p class="copy" style="left:603px;top:805px;width:475px">Lorem Ipsum is simply dummy text of the printing and typesetting industry. Lorem Ipsum has been the industry's standard dummy text ever since the 1500s, when an unknown printer took a galley of type and scrambled it to make a type specimen book. It has survived not only five centuries, but also the leap into electronic typesetting, remaining essentially unchanged.</p>
<a class="btn" href="#" style="left:602px;top:992px;width:138px;height:47px">Read More</a>

<h2 class="section-title" style="left:115px;top:1180px">Premium Quality</h2>
<p class="copy" style="left:115px;top:1237px;width:475px">Lorem Ipsum is simply dummy text of the printing and typesetting industry. Lorem Ipsum has been the industry's standard dummy text ever since the 1500s, when an unknown printer took a galley of type and scrambled it to make a type specimen book. It has survived not only five centuries, but also the leap into electronic typesetting, remaining essentially unchanged.</p>
<a class="btn" href="#" style="left:114px;top:1414px;width:138px;height:47px">Read More</a>
<div class="photo" role="img" aria-label="Brand emblem decoration" style="left:700px;top:1140px;width:290px;height:290px;border-radius:50%;background:radial-gradient(circle,#f6b08c,#f1d9cb)"></div>

<h2 class="section-title" style="left:0;top:1510px;width:1165px;text-align:center">Our Products</h2>

<div class="price-panel">
  <div class="panel-title">Price Range</div>
  <div class="panel-sub">Lorem Ipsum is simply dummy</div>
  <svg class="abs" style="left:14px;top:120px" width="286" height="14" viewBox="0 0 286 14" aria-label="Price slider"><line x1="0" y1="7" x2="286" y2="7" stroke="#ccc" stroke-width="2"/><line x1="47" y1="7" x2="235" y2="7" stroke="#ef7338" stroke-width="2"/><circle cx="47" cy="7" r="5.5" fill="#fff" stroke="#ef7338" stroke-width="2"/><circle cx="235" cy="7" r="5.5" fill="#fff" stroke="#ef7338" stroke-width="2"/></svg>
  <div class="range-label" style="left:14px">$1,000</div>
  <div class="range-label" style="right:18px">$20,000.</div>
  <div class="field-label" style="top:172px">Min Price</div>
  <div class="field" style="top:198px"><span>$1000</span><i></i><b>$</b></div>
  <div class="field-label" style="top:264px">Min Price</div>
  <div class="field" style="top:290px"><span>$20000</span><i></i><b>$</b></div>
</div>

<div class="product" role="img" aria-label="Bright kitchen with a long wooden island and white countertop" style="left:450px;top:1602px;width:675px;height:398px;background:linear-gradient(180deg,#f2f1ee 0%,#e5e2dc 45%,#c9a98a 75%,#d9d6d0 100%)">
  <h3>Lorem Ipsum is simply</h3><p>Lorem Ipsum is simply dummy</p><strong>$1000</strong>
</div>
<div class="product" role="img" aria-label="Dining room with a live-edge wooden table and curved chairs" style="left:98px;top:2038px;width:642px;height:398px;background:linear-gradient(180deg,#f0efec 0%,#e2ded6 50%,#b08a63 78%,#cfc9bf 100%)">
  <h3>Lorem Ipsum is simply</h3><p>Lorem Ipsum is simply dummy</p><strong>$5000</strong>
</div>
<div class="product" role="img" aria-label="Close-up of a carved wooden cabinet door" style="left:769px;top:2038px;width:356px;height:398px;background:linear-gradient(90deg,#ece9e5 0%,#b7956f 45%,#7a4f2a 100%)">
  <h3>Lorem Ipsum is simply</h3><p>Lorem Ipsum is simply dummy</p><strong>$15000</strong>
</div>

<a class="btn" href="#" style="left:534px;top:2488px;width:137px;height:47px">Read More</a>

<div class="feature" style="left:87px">
  <svg width="62" height="62" viewBox="0 0 62 62" aria-label="Quality badge"><circle cx="31" cy="31" r="29" fill="#ef7338"/><circle cx="31" cy="31" r="19" fill="none" stroke="#fff" stroke-width="3"/><path d="M22 31l7 7 12-13" fill="none" stroke="#fff" stroke-width="4"/></svg>
  <h4>Lorem Ipsum is</h4><p>Lorem Ipsum is simply dummy text of the printing and typesetting industry. Lorem Ipsum has been the</p>
</div>
<div class="feature" style="left:359px">
  <svg width="78" height="62" viewBox="0 0 78 62" aria-label="Delivery truck"><rect x="8" y="14" width="42" height="28" rx="3" fill="#ef7338"/><path d="M50 22h14l10 11v9H50z" fill="#ef7338"/><circle cx="20" cy="44" r="6" fill="#ef7338" stroke="#fff" stroke-width="2"/><circle cx="60" cy="44" r="6" fill="#ef7338" stroke="#fff" stroke-width="2"/><line x1="0" y1="22" x2="6" y2="22" stroke="#ef7338" stroke-width="3"/><line x1="0" y1="30" x2="6" y2="30" stroke="#ef7338" stroke-width="3"/></svg>
  <h4>Lorem Ipsum is</h4><p>Lorem Ipsum is simply dummy text of the printing and typesetting industry. Lorem Ipsum has been the</p>
</div>
<div class="feature" style="left:634px">
  <svg width="62" height="62" viewBox="0 0 62 62" aria-label="Secure payment"><rect x="2" y="18" width="44" height="30" rx="3" fill="#ef7338"/><rect x="2" y="25" width="44" height="6" fill="#fff"/><circle cx="44" cy="16" r="13" fill="#fff" stroke="#ef7338" stroke-width="3"/><path d="M38 16l5 5 8-9" fill="none" stroke="#ef7338" stroke-width="3"/></svg>
  <h4>Lorem Ipsum is</h4><p>Lorem Ipsum is simply dummy text of the printing and typesetting industry. Lorem Ipsum has been the</p>
</div>
<div class="feature" style="left:906px">
  <svg width="62" height="62" viewBox="0 0 62 62" aria-label="Award"><circle cx="31" cy="24" r="18" fill="none" stroke="#ef7338" stroke-width="5"/><circle cx="31" cy="24" r="8" fill="#ef7338"/><path d="M18 36l-8 16 9-2 4 8 6-14M44 36l8 16-9-2-4 8-6-14" fill="#ef7338"/></svg>
  <h4>Lorem Ipsum is</h4><p>Lorem Ipsum is simply dummy text of the printing and typesetting industry. Lorem Ipsum has been the</p>
</div>

<section class="promise">
  <h2>We never cut living trees. Trees are<br>harvested, milled, and kiln dried</h2>
  <p>Lorem Ipsum is simply dummy text of the printing and typesetting industry. Lorem Ipsum has been the industry's standard dummy text ever since the 1500s, when an unknown printer took a galley of type and scrambled it to make a type specimen book. It has survived not only five centuries, but also the leap into electronic typesetting, remaining</p>
  <a class="btn btn--outline" href="#" style="left:534px;top:244px;width:137px;height:47px">Read More</a>
</section>

<footer class="site-footer">
  <div class="brand" style="left:493px;top:38px"><span class="brand__dot"></span>Heartwood Tables</div>
  <div class="social"><span aria-label="Social link"></span><span aria-label="Social link"></span><span aria-label="Social link"></span></div>
  <nav class="foot-nav"><span>What We Do</span><span>Our Products</span><span>Shop</span><span>Support</span><span>Contact us</span></nav>
  <div class="copyright">© 2023 Heartwood Tables All rights reserved</div>
</footer>

</body>
</html>
```